Business Card Design for Property Development Company Director

I am looking for a professional and unforgettable business card design for our Director of our Property Development Company.
Please see attached .pptx file to find out what information to include. You don't have to follow the exact format shown in the file - I am interested to see your creative flair using the information provided.

```html
<!DOCTYPE html>
<html lang="en">
<head>
<meta charset="utf-8">
<title>Harwick Property Group – Business Card</title>
<link rel="stylesheet" href="https://fonts.googleapis.com/css2?family=Arimo:wght@400;700&display=swap">
<style>
  :root {
    --page-bg: #2a2b2f;
    --card-bg: #ffffff;
    --brand-blue: #1d4fa8;
    --brand-grey: #5b5c60;
    --text-grey: #4a4b4f;
    --tint: #eef0f5;
    --tint-deep: #e4e8f1;
  }
  * { box-sizing: border-box; margin: 0; padding: 0; }
  html, body { width: 1200px; height: 800px; overflow: hidden; }
  body {
    background: var(--page-bg);
    font-family: "Arimo", Arial, sans-serif;
    display: flex;
    align-items: center;
    justify-content: center;
    gap: 40px;
  }
  .card {
    position: relative;
    width: 540px;
    height: 310px;
    background: var(--card-bg);
    border-radius: 22px;
    overflow: hidden;
  }

  /* Brand name lockup */
  .brand {
    display: flex;
    align-items: center;
    gap: 12px;
  }
  .brand-mark {
    width: 34px;
    height: 34px;
    background: var(--brand-grey);
    flex: none;
  }
  .brand-name {
    color: var(--brand-blue);
    font-weight: 700;
    font-size: 24px;
    line-height: 1.05;
    letter-spacing: 0.5px;
    text-transform: uppercase;
  }

  /* Front */
  .card-front {
    display: flex;
    flex-direction: column;
    align-items: center;
    padding-top: 58px;
  }
  .tagline {
    color: var(--text-grey);
    font-weight: 700;
    font-size: 17px;
    line-height: 1.3;
    text-align: center;
    letter-spacing: 0.3px;
  }
  .card-front .brand { margin-top: 30px; }
  .invite {
    position: absolute;
    bottom: 38px;
    left: 0; right: 0;
    text-align: center;
    font-size: 11px;
    color: var(--text-grey);
  }
  .invite strong { font-weight: 700; }

  /* Back */
  .back-tint {
    position: absolute;
    inset: 0 auto 0 0;
    width: 62%;
    background: linear-gradient(115deg, var(--tint) 0%, var(--tint) 60%, rgba(238,240,245,0) 100%);
  }
  .back-decor {
    position: absolute;
    left: 120px;
    top: 40px;
    width: 200px;
    height: 200px;
    background: var(--tint-deep);
  }
  .card-back .brand {
    position: absolute;
    left: 36px;
    top: 128px;
  }
  .card-back .brand-name { font-size: 22px; }
  .contact {
    position: absolute;
    left: 318px;
    top: 70px;
    width: 200px;
  }
  .person-name {
    font-weight: 700;
    font-size: 19px;
    color: var(--text-grey);
    text-transform: uppercase;
  }
  .person-name .surname { color: var(--brand-blue); }
  .person-role {
    font-size: 14px;
    color: var(--brand-blue);
    margin-top: 2px;
  }
  .contact-list {
    list-style: none;
    margin-top: 14px;
  }
  .contact-list li {
    display: flex;
    align-items: center;
    gap: 8px;
    font-size: 12px;
    color: var(--text-grey);
    margin-bottom: 6px;
  }
  .contact-list svg { width: 12px; height: 12px; fill: var(--brand-blue); flex: none; }
  .licence {
    margin-top: 12px;
    font-size: 11.5px;
    color: var(--brand-blue);
  }
</style>
</head>
<body>

  <section class="card card-front">
    <p class="tagline">PROPERTY DEVELOPMENT<br>&amp; SITE ACQUISITION SPECIALISTS</p>
    <div class="brand">
      <span class="brand-mark"></span>
      <span class="brand-name">Harwick<br>Property Group</span>
    </div>
    <p class="invite">Ask me about our <strong>INVESTMENT &amp; PARTNERSHIP</strong> opportunities</p>
  </section>

  <section class="card card-back">
    <div class="back-tint"></div>
    <div class="back-decor"></div>
    <div class="brand">
      <span class="brand-mark"></span>
      <span class="brand-name">Harwick<br>Property Group</span>
    </div>
    <div class="contact">
      <p class="person-name">Daniel <span class="surname">Carver</span></p>
      <p class="person-role">Director</p>
      <ul class="contact-list">
        <li>
          <svg viewBox="0 0 12 12"><path d="M1 3c0-1 1-2 2-2h6c1 0 2 1 2 2v1H8V3H4v1H1zM2 5h8l1 6H1z"/></svg>
          0400 123 456
        </li>
        <li>
          <svg viewBox="0 0 12 12"><path d="M0 2h12v8H0zM1 3l5 4 5-4v-.2H1z" fill-rule="evenodd"/></svg>
          daniel@harwickgroup.com.au
        </li>
        <li>
          <svg viewBox="0 0 12 12"><circle cx="6" cy="6" r="5.5"/><path d="M0.5 6h11M6 0.5v11" stroke="#fff" stroke-width="0.8"/></svg>
          www.harwickgroup.com.au
        </li>
      </ul>
      <p class="licence">Real Estate Lic: 1234567 &amp; 1234568</p>
    </div>
  </section>

</body>
</html>
```